Creative, fresh business card design for Ripplecraft Facades

We need a fresh, creative business card design for Ripplecraft Facades. We are the manufacturer of Ripplecraft Facades in Australia. Wall panels are 2400 x 1200mm panels made from MDF and feature 3D patterns on the face of the panel. The colours to be used are green, silver/grey and white RGB
Red 187
Green 207
Blue 65.

An idea is to possibly use a watermark of one of our designs as a background (like on the "Grids" design on the left hand side of page 2 of our brochure).

Target Market(s)

Interior designers, architects, builders and home renovators

Industry/Entity Type

Business

Contact Information for Business Card

Details to go on the card are:
Our logo (attached),
Slogan: "Decorative panels for interiors and exteriors",
Contact name,
Position,
Mobile phone number,
Business address,
Business phone,
Business fax,
Website and
Email address.

I have attached a few images of our panels and our brochure for reference.

The colours of the business card should feature our logo colours which are: RGB
Red 187
Green 207
Blue 65

Requirements
Must have
• Very modern fonts and design. Some of the designs shown especially the "Prisms" design which is a popular design.
Nice to have
• Creative but simple design. Very contemporary.
Should not have
• Anything ornate or old fashioned.

```html
<!DOCTYPE html>
<html lang="en">
<head>
<meta charset="utf-8">
<title>Ripplecraft Facades – Business Card</title>
<link href="https://fonts.googleapis.com/css2?family=Montserrat:wght@400;500;700&display=swap" rel="stylesheet">
<style>
  :root {
    --brand-green: #bbcf41;
    --band-grey: #a7a9ab;
    --slogan-grey: #8a8c8e;
    --white: #ffffff;
    --page-bg: #ecebe7;
    --photo-warm: #6b4a32;
    --photo-cool: #c9ccce;
    --prism-light: #f6f6f6;
    --prism-shade: #dcdcdc;
  }
  * { box-sizing: border-box; margin: 0; padding: 0; }
  html, body { width: 1200px; height: 950px; overflow: hidden; }
  body {
    background: var(--page-bg);
    font-family: "Montserrat", Arial, sans-serif;
    display: flex;
    justify-content: center;
    align-items: center;
    gap: 100px;
  }
  .card {
    width: 420px;
    height: 700px;
    position: relative;
    overflow: hidden;
    box-shadow: 0 10px 30px rgba(0,0,0,.18);
  }

  /* Front */
  .card-front { background: var(--brand-green); color: var(--white); }
  .front-logo {
    position: absolute; top: 70px; left: 0; right: 0;
    display: flex; align-items: center; justify-content: center; gap: 12px;
  }
  .logo-square { width: 26px; height: 26px; background: var(--white); }
  .logo-name { font-weight: 700; font-size: 24px; letter-spacing: .5px; }
  .contact {
    position: absolute; top: 180px; left: 0; right: 0;
    text-align: center;
  }
  .contact .icon { display: block; margin: 0 auto 4px; }
  .contact-name { font-weight: 700; font-size: 26px; letter-spacing: 1px; }
  .contact-role { font-size: 17px; margin-bottom: 18px; }
  .contact-line { font-size: 17px; line-height: 1.35; margin-bottom: 14px; }
  .front-band {
    position: absolute; left: 0; right: 0; bottom: 0; height: 120px;
    background: var(--band-grey);
    border-top: 5px solid var(--white);
    display: flex; align-items: center; justify-content: center;
  }
  .website { font-size: 19px; letter-spacing: 2px; }

  /* Back */
  .card-back { background: var(--white); }
  .back-photo {
    position: absolute; top: 0; left: 0; right: 0; height: 350px;
    background: linear-gradient(160deg, var(--photo-warm) 0%, #8a6a4c 35%, var(--photo-cool) 70%, #e8e9ea 100%);
  }
  .back-prisms {
    position: absolute; top: 350px; left: 0; right: 0; bottom: 0;
    background: linear-gradient(135deg, var(--prism-light) 0%, var(--prism-shade) 100%);
  }
  .back-logo {
    position: absolute; top: 470px; left: 0; right: 0;
    text-align: center;
  }
  .back-logo-row {
    display: flex; align-items: center; justify-content: center; gap: 12px;
  }
  .back-logo .logo-square { background: var(--brand-green); }
  .back-logo .logo-name { color: var(--brand-green); }
  .slogan {
    margin-top: 14px; font-size: 15px; font-weight: 500;
    color: var(--slogan-grey); line-height: 1.3;
  }
</style>
</head>
<body>

<section class="card card-front">
  <div class="front-logo">
    <span class="logo-square"></span>
    <span class="logo-name">Ripplecraft Facades</span>
  </div>

  <div class="contact">
    <svg class="icon" width="16" height="16" viewBox="0 0 16 16" aria-hidden="true">
      <circle cx="8" cy="5" r="3.5" fill="var(--white)"/>
      <path d="M1 16c0-4 3-6.5 7-6.5s7 2.5 7 6.5z" fill="var(--white)"/>
    </svg>
    <p class="contact-name">MARA DELLING</p>
    <p class="contact-role">CEO &amp; Founder</p>

    <svg class="icon" width="14" height="18" viewBox="0 0 14 18" aria-hidden="true">
      <path d="M7 0a7 7 0 0 0-7 7c0 5 7 11 7 11s7-6 7-11a7 7 0 0 0-7-7z" fill="var(--white)"/>
      <circle cx="7" cy="7" r="2.5" fill="var(--brand-green)"/>
    </svg>
    <p class="contact-line">412 Fernbrook Road<br>Geelong, Victoria 3220</p>

    <svg class="icon" width="18" height="16" viewBox="0 0 18 16" aria-hidden="true">
      <path d="M4 1l3 3-2 2c1 2 3 4 5 5l2-2 3 3-2 3C7 15 2 9 1 4z" fill="var(--white)"/>
    </svg>
    <p class="contact-line">(555) 210-4471</p>

    <svg class="icon" width="20" height="14" viewBox="0 0 20 14" aria-hidden="true">
      <rect x="0" y="4" width="20" height="10" rx="2" fill="var(--white)"/>
      <rect x="5" y="0" width="10" height="5" fill="var(--white)"/>
    </svg>
    <p class="contact-line">(555) 387-1902</p>

    <svg class="icon" width="20" height="14" viewBox="0 0 20 14" aria-hidden="true">
      <rect x="0" y="0" width="20" height="14" rx="1.5" fill="var(--white)"/>
      <path d="M1 1l9 7 9-7" fill="none" stroke="var(--brand-green)" stroke-width="1.6"/>
    </svg>
    <p class="contact-line">mdelling@ripplecraftfacades.com</p>
  </div>

  <div class="front-band">
    <p class="website">www.ripplecraftfacades.com</p>
  </div>
</section>

<section class="card card-back">
  <div class="back-photo" role="img" aria-label="Photograph of a modern interior with timber ceiling beams, tall windows and green lounge chairs"></div>
  <div class="back-prisms" role="img" aria-label="White three-dimensional prism panel surface"></div>
  <div class="back-logo">
    <div class="back-logo-row">
      <span class="logo-square"></span>
      <span class="logo-name">Ripplecraft Facades</span>
    </div>
    <p class="slogan">decorative panels for<br>interiors &amp; landscapes</p>
  </div>
</section>

</body>
</html>
```